Duct Manufacturing Company new to the industry needs business card and stationary design

we are sheet metal duct manufacturers looking for a business card design to fit my new business logo.
nothing to crazy that will date, but want it to stand out from the crowed.
I'm sure you guys will work it out.

Contact Information for Business Card

Glen Marsh
Director

Address
17 Dorwell St
Larrimore NSW 2697

0438 760 514

Sales@flowbend.com.au

Font styles to use
Other font styles liked:
• BankGothic md bt

Requirements
Nice to have
• Like the idea of corner rounded to match logo
• like to keep colours flowing
• font I like sharp square not rounded

```html
<!DOCTYPE html>
<html lang="en">
<head>
<meta charset="utf-8">
<title>Flowbend Industries – Business Card</title>
<link rel="stylesheet" href="https://fonts.googleapis.com/css2?family=Michroma&family=Montserrat:wght@400;500&display=swap">
<style>
  :root {
    --page-bg: #e4e4e4;
    --card-black: #0d0d0e;
    --card-white: #ffffff;
    --brand-green: #7cc242;
    --brand-blue: #1466b8;
    --wave-blue: #0d4fa3;
    --text-dark: #2b2b2b;
    --text-grey: #6a6a6a;
  }
  * { margin: 0; padding: 0; box-sizing: border-box; }
  html, body { width: 1200px; height: 1200px; overflow: hidden; }
  body {
    background: var(--page-bg);
    display: flex;
    flex-direction: column;
    align-items: center;
    justify-content: center;
    gap: 70px;
  }
  .card {
    position: relative;
    width: 700px;
    height: 428px;
    border-radius: 26px;
    overflow: hidden;
    box-shadow: 0 6px 18px rgba(0,0,0,0.18);
  }
  .card--front { background: var(--card-black); display: flex; align-items: center; justify-content: center; }
  .card--back { background: var(--card-black); }
  .card__backdrop { position: absolute; inset: 0; }

  .wordmark {
    font-family: "Michroma", sans-serif;
    font-weight: 400;
    color: var(--brand-green);
    text-align: center;
    line-height: 1.25;
    letter-spacing: 0.04em;
    display: flex;
    align-items: center;
    gap: 16px;
  }
  .wordmark__dot {
    width: 30px; height: 30px; border-radius: 50%;
    background: var(--brand-green);
    flex: none;
  }
  .wordmark__name { font-size: 34px; }
  .card--back .wordmark {
    position: absolute;
    left: 30px; top: 170px;
    width: 340px;
    justify-content: center;
    gap: 10px;
  }
  .card--back .wordmark__name { font-size: 25px; }
  .card--back .wordmark__dot { width: 22px; height: 22px; }

  .contact {
    position: absolute;
    left: 465px; top: 70px;
    width: 220px;
  }
  .contact__name {
    font-family: "Michroma", sans-serif;
    font-size: 20px;
    font-weight: 400;
    color: var(--brand-blue);
    letter-spacing: 0.06em;
    white-space: nowrap;
  }
  .contact__role {
    font-family: "Montserrat", sans-serif;
    font-size: 13px;
    color: var(--text-grey);
    margin: 6px 0 0 16px;
  }
  .contact__list {
    list-style: none;
    margin-top: 62px;
    font-family: "Montserrat", sans-serif;
    font-size: 14px;
    color: var(--text-dark);
  }
  .contact__item { display: flex; align-items: flex-start; gap: 10px; line-height: 1.45; margin-bottom: 3px; white-space: nowrap; }
  .contact__icon { width: 14px; height: 14px; flex: none; margin-top: 3px; fill: var(--wave-blue); }
</style>
</head>
<body>

  <section class="card card--front" aria-label="Card front">
    <div class="wordmark">
      <span class="wordmark__dot"></span>
      <span class="wordmark__name">FLOWBEND<br>INDUSTRIES</span>
    </div>
  </section>

  <section class="card card--back" aria-label="Card back">
    <svg class="card__backdrop" viewBox="0 0 700 428" width="700" height="428" aria-hidden="true">
      <path d="M330 0 C400 60 420 190 428 290 C433 360 448 410 478 428 L700 428 L700 0 Z" fill="#ffffff"/>
      <path d="M330 0 C400 60 420 190 428 290 C433 360 448 410 478 428" fill="none" stroke="#0d4fa3" stroke-width="4"/>
      <path d="M418 250 C424 300 428 360 446 400 C452 414 460 424 470 428 L452 428 C440 412 430 380 426 330 Z" fill="#0d4fa3"/>
    </svg>

    <div class="wordmark">
      <span class="wordmark__dot"></span>
      <span class="wordmark__name">FLOWBEND<br>INDUSTRIES</span>
    </div>

    <div class="contact">
      <h1 class="contact__name">GLEN MARSH</h1>
      <p class="contact__role">Director</p>
      <ul class="contact__list">
        <li class="contact__item">
          <svg class="contact__icon" viewBox="0 0 16 16"><path d="M2 6 C2 3 5 2 8 2 C11 2 14 3 14 6 L11 7 L10 5 L6 5 L5 7 Z M4 8 L12 8 L14 14 L2 14 Z"/></svg>
          <span>0438 760 514</span>
        </li>
        <li class="contact__item">
          <svg class="contact__icon" viewBox="0 0 16 16"><circle cx="8" cy="8" r="6.5" fill="none" stroke="#0d4fa3" stroke-width="1.5"/><ellipse cx="8" cy="8" rx="2.8" ry="6.5" fill="none" stroke="#0d4fa3" stroke-width="1.2"/><path d="M1.5 8 H14.5" stroke="#0d4fa3" stroke-width="1.2"/></svg>
          <span>flowbend.com.au</span>
        </li>
        <li class="contact__item">
          <svg class="contact__icon" viewBox="0 0 16 16"><path d="M1 3 H15 V13 H1 Z" /><path d="M1.5 3.5 L8 9 L14.5 3.5" fill="none" stroke="#fff" stroke-width="1.4"/></svg>
          <span>Sales@flowbend.com.au</span>
        </li>
        <li class="contact__item">
          <svg class="contact__icon" viewBox="0 0 16 16"><path d="M8 1 C5 1 3 3.2 3 6 C3 10 8 15 8 15 C8 15 13 10 13 6 C13 3.2 11 1 8 1 Z M8 4 A2 2 0 1 0 8.01 4 Z"/></svg>
          <span>17 Dorwell St<br>Larrimore NSW 2697</span>
        </li>
      </ul>
    </div>
  </section>

</body>
</html>
```